Create modern and sleek business card for luxury real estate company

We're a "boutique" real estate office looking for a design that gets across a highly modern luxury brand. Blacks and whites are probably the best colors unless we try a silver foil for the logo. I've attached a version of our current logo here. I'd like to swap out the current font on there with Gotham Light Regular.

I'm looking to have one side of the card have the logo with the space for our agents info on the other side.

Target Market(s)

Young professionals in a "luxury" headspace

Industry/Entity Type

Real estate

Contact Information for Business Card

A place for agent name, cell number, website. The slogan "Quietly Redefining Fine Living".

Font styles to use
Other font styles liked:
• Gotham Regular

Colors

Designer to choose only greyscale colors for use in the design.

Requirements
Must have
• Matte black as the background color. Clean lines and use of contrast. A specific design aspect that will use silver foil.
Nice to have
• Up in the air on integrating a QR code
Should not have
• Any houses or other real estate related design (ex: a clip art house)

```html
<!DOCTYPE html>
<html lang="en">
<head>
<meta charset="utf-8">
<title>Meridian Realty Business Card</title>
<link rel="stylesheet" href="https://fonts.googleapis.com/css2?family=Montserrat:wght@300;400;500&display=swap">
<style>
  :root {
    --backdrop: #1c1c1c;
    --card-black: #0b0b0b;
    --silver: #d4d4d4;
    --silver-soft: #a9a9a9;
    --foil-light: #ececec;
    --foil-dark: #bdbdbd;
    --ink-dark: #1a1a1a;
  }
  * { margin: 0; padding: 0; box-sizing: border-box; }
  html, body { width: 1200px; height: 1200px; overflow: hidden; }
  body {
    background: var(--backdrop);
    font-family: "Montserrat", sans-serif;
    font-weight: 300;
    color: var(--silver);
    position: relative;
  }
  .card {
    position: absolute;
    width: 700px;
    height: 400px;
    background: var(--card-black);
    box-shadow: 0 18px 40px rgba(0,0,0,0.5);
  }
  .card--info { left: 70px; top: 110px; }
  .card--brand { left: 430px; top: 680px; }

  .brand-lockup { display: flex; align-items: center; gap: 18px; }
  .brand-lockup__circle {
    border: 2px solid var(--silver);
    border-radius: 50%;
    flex: none;
  }
  .brand-lockup__name {
    font-weight: 400;
    text-transform: uppercase;
    letter-spacing: 0.06em;
    line-height: 1.15;
    color: var(--silver);
  }

  .card--info .brand-lockup { position: absolute; left: 50px; top: 54px; }
  .card--info .brand-lockup__circle { width: 64px; height: 64px; }
  .card--info .brand-lockup__name { font-size: 26px; }

  .agent { position: absolute; left: 50px; top: 196px; }
  .agent__name { font-size: 26px; font-weight: 400; color: #f0f0f0; }
  .agent__role { font-size: 13px; color: var(--silver-soft); margin-top: 4px; letter-spacing: 0.03em; }

  .contact { position: absolute; left: 50px; top: 262px; list-style: none; }
  .contact__item {
    display: flex; align-items: center; gap: 14px;
    font-size: 12.5px; color: var(--silver); height: 27px;
  }
  .contact__icon { width: 16px; height: 16px; flex: none; }

  .divider {
    position: absolute; left: 420px; top: 70px;
    width: 1px; height: 250px; background: var(--silver-soft);
  }

  .partner { position: absolute; left: 450px; top: 58px; width: 220px; text-align: center; }
  .partner__mark {
    width: 150px; height: 150px; margin: 0 auto;
    background: linear-gradient(135deg, var(--foil-light), var(--foil-dark));
    display: flex; align-items: center; justify-content: center;
    font-size: 24px; font-weight: 400; letter-spacing: 0.12em;
    line-height: 1.2; color: var(--ink-dark); text-align: center;
  }
  .partner__tagline {
    margin-top: 18px; font-size: 17px; letter-spacing: 0.14em;
    line-height: 1.3; color: var(--silver);
  }

  .card--brand .brand-lockup {
    position: absolute; left: 0; right: 0; top: 118px; justify-content: center; gap: 24px;
  }
  .card--brand .brand-lockup__circle { width: 96px; height: 96px; }
  .card--brand .brand-lockup__name { font-size: 40px; }
  .card--brand .website {
    position: absolute; left: 0; right: 0; bottom: 48px;
    text-align: center; font-size: 14px; letter-spacing: 0.22em; color: var(--silver-soft);
  }
</style>
</head>
<body>

<section class="card card--info">
  <div class="brand-lockup">
    <span class="brand-lockup__circle"></span>
    <span class="brand-lockup__name">Meridian<br>Realty</span>
  </div>

  <div class="agent">
    <p class="agent__name">Lorem ipsum</p>
    <p class="agent__role">Company Agent</p>
  </div>

  <ul class="contact">
    <li class="contact__item">
      <svg class="contact__icon" viewBox="0 0 16 16" fill="none" stroke="currentColor" stroke-width="1.1"><path d="M3 1.5h3l1.2 3.2-1.7 1.1a8 8 0 0 0 4.7 4.7l1.1-1.7 3.2 1.2v3a1.5 1.5 0 0 1-1.6 1.5A13 13 0 0 1 1.5 3.1 1.5 1.5 0 0 1 3 1.5z"/></svg>
      555-010-4477
    </li>
    <li class="contact__item">
      <svg class="contact__icon" viewBox="0 0 16 16" fill="none" stroke="currentColor" stroke-width="1.1"><rect x="1" y="3" width="14" height="10"/><path d="M1 3l7 6 7-6"/></svg>
      info@northgateliving.com
    </li>
    <li class="contact__item">
      <svg class="contact__icon" viewBox="0 0 16 16" fill="none" stroke="currentColor" stroke-width="1.1"><path d="M8 15s5-5 5-9a5 5 0 0 0-10 0c0 4 5 9 5 9z"/><circle cx="8" cy="6" r="1.8"/></svg>
      Meridian Realty, 48 Harlow Avenue
    </li>
    <li class="contact__item">
      <svg class="contact__icon" viewBox="0 0 16 16" fill="none" stroke="currentColor" stroke-width="1.1"><path d="M3 2l9 5-4 1.2L6.5 13z"/><path d="M8 8.2l3.5 4.3"/></svg>
      www.northgateliving.com
    </li>
  </ul>

  <span class="divider"></span>

  <div class="partner">
    <div class="partner__mark">STILL<br>POINT</div>
    <p class="partner__tagline">Quietly<br>Redefining Fine<br>Living</p>
  </div>
</section>

<section class="card card--brand">
  <div class="brand-lockup">
    <span class="brand-lockup__circle"></span>
    <span class="brand-lockup__name">Meridian<br>Realty</span>
  </div>
  <p class="website">www.northgateliving.com</p>
</section>

</body>
</html>
```